Oil and Gas Exploration and Production company needs a business card design

We need a business card design using our logo and colors in the logo. We want a mainstream design.

```html
<!DOCTYPE html>
<html lang="en">
<head>
<meta charset="utf-8">
<title>Condor Oil &amp; Gas — Business Card</title>
<link rel="stylesheet" href="https://fonts.googleapis.com/css2?family=Roboto+Slab:wght@400;700;900&display=swap">
<style>
  :root {
    --gold: #c49a2c;
    --gold-light: #d4ab42;
    --ink: #141414;
    --grey: #4a4a4a;
    --paper: #ffffff;
    --backdrop: #ece8e1;
  }
  * { margin: 0; padding: 0; box-sizing: border-box; }
  html, body { width: 1200px; height: 911px; overflow: hidden; }
  body {
    background: var(--backdrop);
    font-family: "Roboto Slab", serif;
    position: relative;
  }
  .card {
    position: absolute;
    width: 540px;
    height: 310px;
    border-radius: 22px;
    overflow: hidden;
    box-shadow: 0 6px 18px rgba(0,0,0,0.18);
  }
  .card-front { left: 60px; top: 140px; }
  .card-back { left: 600px; top: 460px; background: var(--paper); }

  .front-field {
    position: absolute; inset: 0;
    background: linear-gradient(135deg, var(--gold-light), var(--gold));
  }
  .info-disc {
    position: absolute;
    left: 50%; top: 50%;
    width: 250px; height: 250px;
    transform: translate(-50%, -50%);
    border-radius: 50%;
    background: var(--paper);
    display: flex; flex-direction: column;
    align-items: center; justify-content: center;
    text-align: center;
  }
  .person-name {
    font-weight: 700; font-size: 19px; letter-spacing: 1px;
    color: var(--ink);
  }
  .person-role {
    font-size: 13px; letter-spacing: 1px; color: var(--gold);
    margin: 2px 0 14px;
  }
  .contact-block { font-size: 12px; line-height: 1.5; color: var(--grey); }
  .contact-block + .contact-block { margin-top: 10px; }

  .brand {
    position: absolute; left: 0; right: 0; top: 108px;
    display: flex; align-items: center; justify-content: center; gap: 14px;
  }
  .brand-dot {
    width: 30px; height: 30px; border-radius: 50%;
    background: var(--gold);
  }
  .brand-name {
    font-weight: 900; font-size: 40px; color: var(--ink);
  }
  .back-url {
    position: absolute; left: 0; right: 0; bottom: 34px;
    text-align: center;
    font-size: 12px; letter-spacing: 6px; color: var(--grey);
  }
</style>
</head>
<body>
  <section class="card card-front">
    <div class="front-field" role="img" aria-label="Gold background with radiating sun-ray decoration"></div>
    <div class="info-disc">
      <p class="person-name">DANIEL REYES</p>
      <p class="person-role">CEO/FOUNDER</p>
      <div class="contact-block">
        <p>2140 Birchwood Road</p>
        <p>Fairbanks, Alaska 99701</p>
      </div>
      <div class="contact-block">
        <p>555 210 4876</p>
        <p>info@condoroilgas.com</p>
        <p>www.condoroilgas.com</p>
      </div>
    </div>
  </section>

  <section class="card card-back">
    <div class="brand">
      <span class="brand-dot"></span>
      <span class="brand-name">Condor Oil &amp; Gas</span>
    </div>
    <p class="back-url">www.condoroilgas.com</p>
  </section>
</body>
</html>
```